RTavenor Business Cards & Letterhead

I have a logo but need a design for some new business cards. We are a Design-Build Firm that specializes in the design and construction of commercial projects.
the cards need to be professional. no cartoon stuff.
i would like to have the cards in AI format so I can update the card as needed. Logo is provided.
Our Address is: 4187 Marlowe Ct. Orin, West Harlowen 27614

```html
<!DOCTYPE html>
<html lang="en">
<head>
<meta charset="utf-8">
<title>RTavenor Business Cards</title>
<link href="https://fonts.googleapis.com/css2?family=Montserrat:wght@400;500;700;800&display=swap" rel="stylesheet">
<style>
  :root {
    --stage: #4a4a4a;
    --card-dark: #1c1c1d;
    --card-light: #ffffff;
    --brand-blue: #0f6ab0;
    --brand-blue-deep: #0a4f8a;
    --logo-grey: #3b3b3d;
    --text-light: #f2f2f2;
    --divider: #6a6a6a;
  }
  * { margin: 0; padding: 0; box-sizing: border-box; }
  html, body { width: 1200px; height: 1200px; overflow: hidden; }
  body {
    background: var(--stage);
    font-family: "Montserrat", Arial, sans-serif;
    display: flex;
    flex-direction: column;
    align-items: center;
    justify-content: center;
    gap: 70px;
  }
  .card {
    position: relative;
    width: 860px;
    height: 491px;
    border-radius: 34px;
    overflow: hidden;
    box-shadow: 0 18px 40px rgba(0,0,0,0.45);
  }
  .card-front { background: var(--card-dark); }
  .front-top {
    position: absolute;
    left: 0; top: 0;
    width: 100%; height: 262px;
    background: var(--card-light);
    display: flex; align-items: center; justify-content: center;
  }
  .accent-rule {
    position: absolute; left: 0; width: 100%;
    background: var(--brand-blue);
  }
  .accent-rule.thin { top: 268px; height: 4px; }
  .accent-rule.thick { top: 262px; height: 4px; background: var(--brand-blue-deep); }
  .brand { display: flex; align-items: center; gap: 16px; }
  .brand-mark { width: 62px; height: 62px; background: var(--brand-blue); }
  .brand-name {
    font-weight: 800;
    font-size: 86px;
    letter-spacing: 1px;
    line-height: 1;
  }
  .card-front .brand-name { color: var(--logo-grey); }
  .card-back .brand-name { color: var(--card-light); }
  .holder {
    position: absolute; left: 70px; top: 345px;
    border-left: 6px solid var(--brand-blue);
    padding-left: 16px;
  }
  .holder-name {
    color: var(--brand-blue);
    font-size: 34px; font-weight: 500; line-height: 1.05;
  }
  .holder-role {
    color: var(--text-light);
    font-size: 20px; font-weight: 400; letter-spacing: 0.5px;
  }
  .divider {
    position: absolute; left: 430px; top: 310px;
    width: 1px; height: 130px; background: var(--divider);
  }
  .contact {
    position: absolute; left: 470px; top: 300px;
    list-style: none;
    color: var(--text-light);
    font-size: 19px; line-height: 1.3;
  }
  .contact li { display: flex; align-items: flex-start; gap: 12px; margin-bottom: 6px; }
  .contact svg { width: 20px; height: 20px; flex: none; margin-top: 2px; }
  .card-back {
    background: var(--card-dark);
    display: flex; align-items: center; justify-content: center;
  }
  .card-back .brand-mark { width: 74px; height: 74px; }
  .card-back .brand-name { font-size: 100px; }
</style>
</head>
<body>
  <section class="card card-front">
    <div class="front-top">
      <div class="brand">
        <span class="brand-mark"></span>
        <span class="brand-name">RTAVENOR</span>
      </div>
    </div>
    <div class="accent-rule thick"></div>
    <div class="accent-rule thin"></div>
    <div class="holder">
      <div class="holder-name">FULL NAME</div>
      <div class="holder-role">POSITION</div>
    </div>
    <div class="divider"></div>
    <ul class="contact">
      <li>
        <svg viewBox="0 0 24 24" aria-hidden="true"><path fill="#0f6ab0" d="M6.6 10.8a15.1 15.1 0 0 0 6.6 6.6l2.2-2.2c.3-.3.7-.4 1-.2 1.1.4 2.3.6 3.6.6.6 0 1 .4 1 1V20c0 .6-.4 1-1 1A17 17 0 0 1 3 4c0-.6.4-1 1-1h3.5c.6 0 1 .4 1 1 0 1.3.2 2.5.6 3.6.1.3 0 .7-.2 1z"/></svg>
        <span>(000) 000 0000</span>
      </li>
      <li>
        <svg viewBox="0 0 24 24" aria-hidden="true"><rect x="2" y="5" width="20" height="14" fill="#0f6ab0"/><path d="M2 5l10 8 10-8" fill="none" stroke="#1c1c1d" stroke-width="1.6"/></svg>
        <span>email@company.com</span>
      </li>
      <li>
        <svg viewBox="0 0 24 24" aria-hidden="true"><path fill="#0f6ab0" d="M12 2a7 7 0 0 0-7 7c0 5.2 7 13 7 13s7-7.8 7-13a7 7 0 0 0-7-7zm0 9.5a2.5 2.5 0 1 1 0-5 2.5 2.5 0 0 1 0 5z"/></svg>
        <span>4187 Marlowe Ct. Orin<br>West Harlowen 27614</span>
      </li>
    </ul>
  </section>

  <section class="card card-back">
    <div class="brand">
      <span class="brand-mark"></span>
      <span class="brand-name">RTAVENOR</span>
    </div>
  </section>
</body>
</html>
```